Corvena Hotel, city center modern minimal hotel operating all year round, on Rhodes island Greece

city, modern ,all year operating hotel

Target Market(s)

tourists, business agents

Industry/Entity Type

tourism

Number of Pages Required

2 page

Requirements
Must have
• room type photos and descriptions, amenities individual listing (graphic), comments sections, map driving location details
Nice to have
• gallery section, modern and minimal design, amenities section, individual room type descriptions, photos and facilities

```html
<!DOCTYPE html>
<html lang="en">
<head>
<meta charset="utf-8">
<title>Corvena Hotel</title>
<link href="https://fonts.googleapis.com/css2?family=Heebo:wght@500;700&family=Montserrat:ital,wght@0,400;0,500;0,600;0,700;1,400&family=Great+Vibes&display=swap" rel="stylesheet">
<style>
:root{
  --navy:#161b31;
  --navy-2:#1e2440;
  --gold:#c4a07a;
  --gold-soft:rgba(196,160,122,.45);
  --ink:#222;
  --muted:#777;
  --line:#e4e4e4;
  --band:#f4f4f4;
  --white:#fff;
  --map-land:#2a3150;
  --map-road:#4a5275;
}
*{margin:0;padding:0;box-sizing:border-box}
html,body{width:1200px;height:3745px;overflow:hidden}
body{position:relative;background:var(--white);font-family:'Montserrat',sans-serif;color:var(--ink)}
.abs{position:absolute}
.heading{font-family:'Heebo',sans-serif;font-weight:700;color:var(--ink)}
.script{font-family:'Great Vibes',cursive;color:var(--gold-soft);font-weight:400;white-space:nowrap}

/* header */
.site-header{left:0;top:0;width:1200px;height:88px;background:var(--navy)}
.brand{display:flex;align-items:center;gap:12px;color:var(--white);font-family:'Montserrat',sans-serif;font-weight:500;font-size:24px;letter-spacing:1px;white-space:nowrap}
.brand-mark{width:26px;height:26px;background:var(--gold)}
.nav-item{top:36px;font-size:12.5px;color:var(--white);text-transform:uppercase;white-space:nowrap}
.nav-item.active{text-decoration:underline;text-underline-offset:4px}
.lang{left:899px;top:37px;font-size:11px;color:var(--white);font-weight:600}
.btn-book{left:982px;top:21px;width:132px;height:45px;border:2px solid var(--gold);border-radius:3px;color:var(--gold);font-size:12px;font-weight:600;display:flex;align-items:center;justify-content:center}

/* hero */
.hero{left:0;top:88px;width:1200px;height:447px;background:linear-gradient(180deg,#1d2f55 0%,#3b4a5c 40%,#5c4a2e 70%,#2a2c22 100%)}
.hero-script{left:0;top:150px;width:1200px;text-align:center;font-size:78px;color:var(--white)}
.hero-title{left:0;top:273px;width:1200px;text-align:center;font-family:'Heebo',sans-serif;font-weight:700;font-size:36px;color:var(--white)}
.booking{left:157px;top:409px;width:886px;height:56px;display:flex}
.booking .field{background:var(--white);border-right:1px solid var(--line);display:flex;align-items:center;justify-content:space-between;padding:0 14px 0 12px;font-size:14px;color:#333}
.booking .check{background:var(--navy);color:var(--white);font-size:12px;font-weight:600;display:flex;align-items:center;justify-content:center}

/* welcome */
.welcome-script{left:84px;top:585px;font-size:90px}
.welcome-title{left:86px;top:664px;font-size:40px;line-height:38px}
.welcome-text{width:327px;font-size:12px;line-height:21px;color:var(--muted)}

/* services */
.service{top:892px;width:300px;height:506px}
.service .label{position:absolute;left:0;top:281px;width:100%;text-align:center;color:var(--white);font-family:'Montserrat',sans-serif;font-weight:700;font-size:19px;text-transform:uppercase;white-space:nowrap}
.service svg{position:absolute;left:118px;top:175px}

/* features */
.features{left:0;top:1398px;width:1200px;height:209px;background:var(--band)}
.feature{top:1468px;width:330px;display:flex;gap:22px}
.feature h3{font-family:'Montserrat',sans-serif;font-weight:600;font-size:20px;color:#2b2b2b;margin-bottom:4px;white-space:nowrap}
.feature p{width:240px;font-size:12.5px;line-height:17.5px;color:var(--muted)}

/* rooms */
.section-script{left:0;width:1200px;text-align:center;font-size:100px}
.section-title{left:0;width:1200px;text-align:center;font-size:40px}
.room{top:1842px;width:307px;height:463px;border:1px solid var(--line);background:var(--white)}
.room .photo{height:208px}
.room h3{position:absolute;left:26px;top:232px;font-size:19px;font-weight:600;color:#2b2b2b;white-space:nowrap}
.room .occ{position:absolute;left:26px;top:272px;font-size:12px;font-style:italic;color:var(--muted);display:flex;gap:8px;align-items:center;white-space:nowrap}
.room .desc{position:absolute;left:26px;top:305px;width:256px;font-size:12px;line-height:21px;color:var(--muted)}
.room .cta{position:absolute;left:26px;top:389px;width:252px;height:43px;border:2px solid var(--gold);border-radius:3px;color:var(--gold);font-size:12px;display:flex;align-items:center;justify-content:center}
.pager{display:flex}
.pager span{width:38px;height:38px;border:1px solid var(--line);display:flex;align-items:center;justify-content:center;font-size:16px;color:#333;background:var(--white)}

/* side tools */
.tools{left:1145px;top:1799px;width:55px;height:157px;background:var(--white);box-shadow:0 2px 10px rgba(0,0,0,.15);display:flex;flex-direction:column;align-items:center;justify-content:space-evenly}

/* dining */
.dining-photo{left:0;top:2432px;width:600px;height:376px;background:radial-gradient(ellipse at 45% 40%,#5a3320 0%,#2e1d14 55%,#1a1410 100%)}
.dining-panel{left:600px;top:2432px;width:600px;height:376px;background:radial-gradient(ellipse at 30% 80%,#4a3e35 0%,#2a2622 55%,#1c1a18 100%)}
.dining-script{left:658px;top:2448px;font-size:72px}
.dining-title{left:665px;top:2508px;font-size:29px;line-height:38px;color:var(--white)}
.dining-text{left:658px;top:2598px;width:262px;font-size:8.5px;line-height:19px;color:var(--white)}
.btn-small{left:649px;top:2687px;width:81px;height:29px;background:var(--gold);color:var(--white);font-size:8.5px;font-weight:600;display:flex;align-items:center;justify-content:center}

/* testimonials */
.avatar{left:557px;top:3017px;width:86px;height:86px;border-radius:50%;background:linear-gradient(135deg,#9aa5ab,#2f5870)}
.author{left:0;top:3132px;width:1200px;text-align:center;font-size:17px;font-weight:500;color:#2b2b2b}
.quote{left:300px;top:3168px;width:600px;text-align:center;font-size:17px;line-height:31px;font-style:italic;color:var(--muted)}
.dot{left:591px;top:3359px;width:17px;height:17px;border-radius:50%;background:#888}

/* footer */
.site-footer{left:0;top:3408px;width:1200px;height:337px;background:var(--navy)}
.footer-text{font-size:14px;line-height:21px;color:#a9adbd}
.footer-head{font-size:12px;font-weight:600;color:var(--white);text-transform:uppercase;white-space:nowrap}
.newsletter{left:612px;top:3527px;width:237px;height:34px;background:var(--white);display:flex;align-items:center;justify-content:space-between;padding:0 12px;font-size:12px;color:#999}
.location-map{left:884px;top:3500px;width:230px;height:112px;background:var(--map-land);border:1px solid var(--map-road)}
.map-pin{left:990px;top:3530px}
.directions{left:884px;top:3620px;width:230px;font-size:11.5px;line-height:17px;color:#a9adbd}
.footer-rule{left:86px;top:3689px;width:1028px;height:1px;background:#3a4060}
.copyright{left:0;top:3708px;width:1200px;text-align:center;font-size:12px;color:#a9adbd}
</style>
</head>
<body>

<header class="abs site-header">
  <div class="abs brand" style="left:68px;top:30px"><span class="brand-mark"></span>Corvena Hotel</div>
  <nav>
    <span class="abs nav-item active" style="left:357px">Home</span>
    <span class="abs nav-item" style="left:429px">Rooms &amp; Suits</span>
    <span class="abs nav-item" style="left:558px">News</span>
    <span class="abs nav-item" style="left:630px">Gallery</span>
    <span class="abs nav-item" style="left:720px">About</span>
    <span class="abs nav-item" style="left:797px">Contact</span>
  </nav>
  <div class="abs lang">EN ⌄</div>
  <div class="abs btn-book">BOOK NOW</div>
</header>

<section class="abs hero" role="img" aria-label="Hotel building lit at dusk with palm trees and a pool"></section>
<div class="abs script hero-script">Book Today</div>
<h1 class="abs hero-title">HOT WEEKEND OFFER</h1>
<div class="abs booking">
  <div class="field" style="width:316px">21 Oct 2022 - 22 Oct 2022
    <svg width="16" height="16" viewBox="0 0 16 16" fill="none" stroke="#777"><rect x="2" y="3" width="12" height="11"/><path d="M2 7h12M5 1v4M11 1v4"/></svg></div>
  <div class="field" style="width:180px">Guests <span>⌄</span></div>
  <div class="field" style="width:179px">Children <span>⌄</span></div>
  <div class="check" style="width:211px">CHECK RATES</div>
</div>

<div class="abs script welcome-script">Welcome</div>
<h2 class="abs heading welcome-title">Enjoy Your Stay<br>in Our Hotel</h2>
<p class="abs welcome-text" style="left:438px;top:656px">Elit, sed do eiusmod tempor incididunt ut labore et dolore magna aliqua. Elit, sed do eiusmod tempor incididunt ut labore et dolore magna aliqua. Elit, sed do eiusmod tempor incididunt ut labore et dolore magna aliqua. Lorem ipsum dolor sit amet, consectetur adipisicing elit,</p>
<p class="abs welcome-text" style="left:789px;top:656px">Elit, sed do eiusmod tempor incididunt ut labore et dolore magna aliqua. Elit, sed do eiusmod tempor incididunt ut labore et dolore magna aliqua. Elit, sed do eiusmod tempor incididunt ut labore et dolore magna aliqua.</p>

<div class="abs service" style="left:0;background:linear-gradient(160deg,#6f7780,#3c3f44)" role="img" aria-label="Hotel bedroom with city view">
  <svg width="64" height="72" viewBox="0 0 64 72" fill="none" stroke="#c4a07a" stroke-width="2"><rect x="6" y="30" width="18" height="40"/><rect x="30" y="22" width="22" height="48"/><path d="M10 30v-10h10v10M36 22V6h10v16"/></svg>
  <div class="label">24H Room Service</div>
</div>
<div class="abs service" style="left:300px;background:linear-gradient(160deg,#3a3430,#1a1614)" role="img" aria-label="Dessert and champagne glasses at the bar">
  <svg width="64" height="72" viewBox="0 0 64 72" fill="none" stroke="#c4a07a" stroke-width="2"><path d="M8 4h16l-3 22a5 5 0 0 1-10 0zM16 31v36M40 4v64M34 4v14h12V4M54 4v64"/></svg>
  <div class="label">Restaurant and Bars</div>
</div>
<div class="abs service" style="left:600px;background:linear-gradient(160deg,#8a8580,#4a4744)" role="img" aria-label="Meeting room with long table and chairs">
  <svg width="70" height="64" viewBox="0 0 70 64" fill="none" stroke="#c4a07a" stroke-width="2"><rect x="4" y="8" width="60" height="52"/><path d="M4 20h60M16 2v12M52 2v12"/><circle cx="20" cy="32" r="3"/><circle cx="34" cy="32" r="3"/><circle cx="48" cy="32" r="3"/><circle cx="20" cy="46" r="3"/><circle cx="34" cy="46" r="3"/></svg>
  <div class="label">Events and Meetings</div>
</div>
<div class="abs service" style="left:900px;background:linear-gradient(160deg,#7c838d,#3e4450)" role="img" aria-label="Woman exercising at the fitness centre">
  <svg width="64" height="72" viewBox="0 0 64 72" fill="none" stroke="#c4a07a" stroke-width="2"><path d="M32 6c12 16 18 26 18 36a18 18 0 0 1-36 0c0-10 6-20 18-36z"/><path d="M4 58c18 10 38 10 56 0"/></svg>
  <div class="label">Fitness and Spa</div>
</div>

<section class="abs features"></section>
<div class="abs feature" style="left:84px">
  <svg width="52" height="46" viewBox="0 0 52 46" fill="none" stroke="#333" stroke-width="1.6"><rect x="6" y="2" width="40" height="32" rx="2"/><path d="M2 40h48M18 18a11 11 0 0 1 16 0M22 22a5 5 0 0 1 8 0"/><circle cx="26" cy="27" r="1.5"/></svg>
  <div><h3>Enjoy free Wi-Fi</h3><p>We believe that when<br>a <i>hotel</i> advertises <i>free WiFi</i>, they should provide travelers with a fast and reliable connection.</p></div>
</div>
<div class="abs feature" style="left:436px">
  <svg width="52" height="46" viewBox="0 0 52 46" fill="none" stroke="#333" stroke-width="1.6"><path d="M6 32a20 20 0 0 1 40 0zM2 36h48M26 12V6M22 6h8"/></svg>
  <div><h3>Concierge service</h3><p>Top-tier hotels have a lot to recommend them: luxurious spas, twice-daily room service and superb on-site restaurants.</p></div>
</div>
<div class="abs feature" style="left:787px">
  <svg width="52" height="46" viewBox="0 0 52 46" fill="none" stroke="#333" stroke-width="1.6"><path d="M2 24h48M2 32c6-4 10 4 16 0s10 4 16 0 10 4 16 0M2 40c6-4 10 4 16 0s10 4 16 0 10 4 16 0M30 24V4h12M42 4v20M30 12h12M30 18h12"/><rect x="6" y="12" width="16" height="12"/></svg>
  <div><h3>Pool access</h3><p>Hotel has pool room, in particular, hotels based in big cities might require keycard access to get into the pool. Spa, and amenity access.</p></div>
</div>

<div class="abs script section-script" style="top:1660px">Comfort</div>
<h2 class="abs heading section-title" style="top:1730px">Best Rooms</h2>

<article class="abs room" style="left:115px">
  <div class="photo" style="background:linear-gradient(160deg,#d9d2c8,#a89a86)" role="img" aria-label="Bright lounge with armchairs and floor lamp"></div>
  <h3>Deluxe Dark Room</h3>
  <div class="occ"><svg width="24" height="14" viewBox="0 0 24 14" fill="none" stroke="#999"><circle cx="7" cy="4" r="3"/><circle cx="16" cy="4" r="3"/><path d="M1 13a6 6 0 0 1 12 0M10 13a6 6 0 0 1 12 0"/></svg>3 adult(s) and 2 child(ren)</div>
  <p class="desc">This comfortable, modern hotel is set in the urban center of Rhodes Town, 10 min-utes' wa...</p>
  <div class="cta">Book now $0.00</div>
</article>
<article class="abs room" style="left:447px">
  <div class="photo" style="background:linear-gradient(160deg,#8d9196,#4e5257)" role="img" aria-label="Bedroom with bedside table and lamp"></div>
  <h3>Standart Big Room</h3>
  <div class="occ"><svg width="24" height="14" viewBox="0 0 24 14" fill="none" stroke="#999"><circle cx="7" cy="4" r="3"/><circle cx="16" cy="4" r="3"/><path d="M1 13a6 6 0 0 1 12 0M10 13a6 6 0 0 1 12 0"/></svg>4 adult(s) and 3 child(ren)</div>
  <p class="desc">Ah, the humble studio apartment. At one time, this dwelling was considered to be the ho...</p>
  <div class="cta">Book now from $25.00</div>
</article>
<article class="abs room" style="left:780px">
  <div class="photo" style="background:linear-gradient(160deg,#b5aea6,#5d544c)" role="img" aria-label="Room with bed, desk and dining table"></div>
  <h3>Standart One Person R...</h3>
  <div class="occ"><svg width="24" height="14" viewBox="0 0 24 14" fill="none" stroke="#999"><circle cx="7" cy="4" r="3"/><circle cx="16" cy="4" r="3"/><path d="M1 13a6 6 0 0 1 12 0M10 13a6 6 0 0 1 12 0"/></svg>2 adult(s) and 3 child(ren)</div>
  <p class="desc">The classic room is equipped with desk and chair, 2 single beds, TV and plenty of stora...</p>
  <div class="cta">Book now from $10.00</div>
</article>
<div class="abs pager" style="left:561px;top:2333px"><span>‹</span><span>›</span></div>

<aside class="abs tools">
  <svg width="22" height="20" viewBox="0 0 22 20" fill="none" stroke="#222" stroke-width="1.6"><rect x="1" y="1" width="20" height="13"/><path d="M7 19h8M11 14v5"/></svg>
  <svg width="20" height="20" viewBox="0 0 20 20" fill="none" stroke="#222" stroke-width="1.6"><circle cx="10" cy="10" r="8.5"/><path d="M1.5 10h17M10 1.5v17"/></svg>
  <svg width="22" height="20" viewBox="0 0 22 20" fill="none" stroke="#222" stroke-width="1.6"><path d="M1 2h4l2 11h11l2-8H6"/><circle cx="8" cy="17" r="1.5"/><circle cx="17" cy="17" r="1.5"/></svg>
</aside>

<div class="abs dining-photo" role="img" aria-label="Grilled steak with rosemary on a wooden board"></div>
<div class="abs dining-panel" role="img" aria-label="Dark table with fork and bowl of salt"></div>
<div class="abs script dining-script">Delicious</div>
<h2 class="abs heading dining-title">Good time, Great<br>taste</h2>
<p class="abs dining-text">Elit, sed do eiusmod tempor incididunt ut labore et dolore magna aliqua. Elit, sed do eiusmod tempor incididunt ut labore et dolore magna aliqua. Elit, sed do eiusmod tempor incididunt ut labore et dolore magna aliqua</p>
<div class="abs btn-small">BOOK NOW</div>

<div class="abs script section-script" style="top:2850px">Testimonials</div>
<h2 class="abs heading section-title" style="top:2910px">What They Say</h2>
<div class="abs avatar" role="img" aria-label="Guest portrait"></div>
<div class="abs author">MARTEN K. HOLLOWAY</div>
<p class="abs quote">Amet, consectetur adipisicing elit, sed do eiusmod incididunt ut labore et dolore magna aliqua. Ut enim minim veniam, ...</p>
<div class="abs pager" style="left:559px;top:3270px"><span>‹</span><span>›</span></div>
<div class="abs dot"></div>

<footer class="abs site-footer"></footer>
<div class="abs brand" style="left:90px;top:3452px"><span class="brand-mark"></span>Corvena Hotel</div>
<p class="abs footer-text" style="left:86px;top:3521px;width:240px">We always strive for growth and development as Brightloom Studio. We don't want to have a large team, we want to have a team that works in unity. Our slogan is "Every day is the last day".</p>
<div class="abs footer-head" style="left:349px;top:3471px">Contact Us</div>
<p class="abs footer-text" style="left:349px;top:3521px;width:240px">27 Ierou Lochou St,<br>Rhodes Town 85100, Greece<br>Tel.: +30 22410 55014<br>Fax.: +30 22410 55015<br><span style="display:block;margin-top:8px">stay@corvenahotel.example</span></p>
<div class="abs footer-head" style="left:612px;top:3471px">Stay in Touch</div>
<div class="abs newsletter">Your email address
  <svg width="16" height="12" viewBox="0 0 16 12" fill="none" stroke="#333" stroke-width="1.5"><path d="M1 6h13M9 1l5 5-5 5"/></svg></div>
<p class="abs footer-text" style="left:612px;top:3576px;width:240px">Enter your email address for promotions and news.</p>

<div class="abs footer-head" style="left:884px;top:3471px">Find Us</div>
<div class="abs location-map" role="img" aria-label="Map of Rhodes Town showing the hotel location and the road from the airport"></div>
<svg class="abs map-pin" width="18" height="24" viewBox="0 0 18 24" fill="#c4a07a"><path d="M9 0a9 9 0 0 1 9 9c0 7-9 15-9 15S0 16 0 9a9 9 0 0 1 9-9z"/><circle cx="9" cy="9" r="3.5" fill="#161b31"/></svg>
<p class="abs directions">By car: 15 km from Rhodes Airport, about 20 min on the coastal road. Free guest parking.</p>

<div class="abs footer-rule"></div>
<div class="abs copyright">Copyright 2022 Corvena Hotel, All rights reserved.</div>

</body>
</html>
```